Wandering Rooms Stationary Set

Wandering Rooms is a bespoke interior design firm set to provide services to VIP clients with elegance and minimalism is the main theme for our stationary set. We require a full stationary set covering A4 letterhead, A4 & A3 envelopes, business cards, USB's, CDs, email signature and any other item the designer sees fit. logo is already designed and finalized, and we require the designer to use it as is without modifying the logo.

Address to be used on letterhead / business cards ...etc shall be as follows:

Phone : +971 2 518 2047
P.O. Box : 309186
Address: Block C&D, Bldg. 47, Court 12, Abu Dhabi, United Arab Emirates
Website: www.wanderingrooms-example.com

Target Market(s)

VIP Clients

Industry/Entity Type

Interior Design

Font styles to use
Other font styles liked:
• something to be unique

Colors

Designer to choose colors to be used in the design.

Requirements
Must have
• Elegant, minimalistic
Nice to have
• Simple yet elegant design having a sharp yet clean cut format
Should not have
• No additional colours, just colours that are used in the logo (silver, black or gold)

```html
<!DOCTYPE html>
<html lang="en">
<head>
<meta charset="utf-8">
<title>Wandering Rooms – Business Card</title>
<link href="https://fonts.googleapis.com/css2?family=Cormorant+Garamond:wght@400;600&family=Roboto:wght@400&display=swap" rel="stylesheet">
<style>
  :root {
    --backdrop: #e9e9e7;
    --card-grey: #9b9b97;
    --card-cream: #f4f1e3;
    --cream-ink: #f3f0dc;
    --grey-ink: #8e8e8a;
    --dark-ink: #3c3c3a;
    --icon-grey: #8a8a86;
  }
  * { margin: 0; padding: 0; box-sizing: border-box; }
  html, body { width: 1200px; height: 787px; overflow: hidden; background: var(--backdrop); }
  .sheet {
    width: 1200px; height: 787px;
    display: flex; align-items: center; justify-content: center; gap: 60px;
  }
  .card {
    width: 530px; height: 303px;
    box-shadow: 0 6px 18px rgba(0,0,0,0.18);
    position: relative;
  }
  .card--front {
    background: var(--card-grey);
    display: flex; flex-direction: column; align-items: center; justify-content: center;
  }
  .brand-name {
    font-family: "Cormorant Garamond", serif;
    font-weight: 400;
    letter-spacing: 0.04em;
  }
  .card--front .brand-name { font-size: 50px; color: var(--cream-ink); }
  .front-url {
    margin-top: 26px;
    font-family: "Roboto", sans-serif; font-size: 12px; letter-spacing: 0.12em;
    color: var(--cream-ink);
  }
  .card--back { background: var(--card-cream); }
  .back-logo {
    position: absolute; left: 34px; top: 62px; width: 200px;
    text-align: center;
  }
  .card--back .brand-name { font-size: 32px; color: var(--grey-ink); line-height: 1.1; }
  .divider {
    position: absolute; left: 262px; top: 48px; width: 1px; height: 150px;
    background: var(--grey-ink);
  }
  .contact { position: absolute; left: 288px; top: 52px; }
  .person-name {
    font-family: "Cormorant Garamond", serif; font-weight: 600;
    font-size: 21px; letter-spacing: 0.06em; color: var(--grey-ink);
  }
  .person-title {
    font-family: "Roboto", sans-serif; font-size: 13px; color: var(--dark-ink);
    margin-top: 2px;
  }
  .contact-list { list-style: none; margin-top: 20px; }
  .contact-list li, .address {
    display: flex; align-items: center; gap: 7px;
    font-family: "Roboto", sans-serif; font-size: 12.5px; color: var(--dark-ink);
    line-height: 20px;
  }
  .icon { width: 13px; height: 13px; flex: none; }
  .address { position: absolute; left: 34px; bottom: 38px; }
</style>
</head>
<body>
<main class="sheet">
  <section class="card card--front" aria-label="Card front">
    <div class="brand-name">Wandering Rooms</div>
    <div class="front-url">www.wanderingrooms-example.com</div>
  </section>

  <section class="card card--back" aria-label="Card back">
    <div class="back-logo"><div class="brand-name">Wandering Rooms</div></div>
    <div class="divider"></div>
    <div class="contact">
      <div class="person-name">MARCUS HALE</div>
      <div class="person-title">Gerente General</div>
      <ul class="contact-list">
        <li>
          <svg class="icon" viewBox="0 0 14 14"><circle cx="7" cy="7" r="7" fill="var(--icon-grey)"/><path d="M4.5 3.8c.4-.3.8-.2 1 .2l.6 1.1c.2.3.1.6-.2.8l-.4.3c.3.8.9 1.4 1.7 1.8l.3-.4c.2-.3.5-.4.8-.2l1.1.6c.4.2.5.6.2 1l-.4.5c-.4.4-1 .5-1.6.3C5.9 9 4.9 8 4.2 6.3c-.2-.6 0-1.2.3-1.6z" fill="#fff"/></svg>
          +971 2 518 2047
        </li>
        <li>
          <svg class="icon" viewBox="0 0 14 14"><circle cx="7" cy="7" r="7" fill="var(--icon-grey)"/><rect x="3.5" y="4.5" width="7" height="5" fill="none" stroke="#fff" stroke-width="0.9"/><path d="M3.5 4.7 7 7.3l3.5-2.6" fill="none" stroke="#fff" stroke-width="0.9"/></svg>
          info@wanderingrooms-example.com
        </li>
        <li>
          <svg class="icon" viewBox="0 0 14 14"><circle cx="7" cy="7" r="7" fill="var(--icon-grey)"/><circle cx="7" cy="7" r="3.6" fill="none" stroke="#fff" stroke-width="0.9"/><path d="M3.4 7h7.2M7 3.4c-1.6 2.2-1.6 5 0 7.2M7 3.4c1.6 2.2 1.6 5 0 7.2" fill="none" stroke="#fff" stroke-width="0.8"/></svg>
          www.wanderingrooms-example.com
        </li>
      </ul>
    </div>
    <div class="address">
      <svg class="icon" viewBox="0 0 14 14"><circle cx="7" cy="7" r="7" fill="var(--icon-grey)"/><path d="M7 3a2.6 2.6 0 0 0-2.6 2.6C4.4 7.6 7 11 7 11s2.6-3.4 2.6-5.4A2.6 2.6 0 0 0 7 3z" fill="#fff"/><circle cx="7" cy="5.6" r="1" fill="var(--icon-grey)"/></svg>
      Block C&amp;D, Bldg. 47, Court 12, Abu Dhabi, United Arab Emirates
    </div>
  </section>
</main>
</body>
</html>
```